Master Label Design for Velmora Botanic Products

Looking to update product labels and add consistency across our line with a new master label design. 'Velmora Botanic' has been a trusted name in the health marketplace providing quality herbal and dietary supplements since 1979. We have 8 products in need of a master label design, examples of our current labels are attached, and you can see more at our website, VelmoraBotanic.com. All 8 products currently have a 160mm x 58mm label size, while 3 products also have a 194mm x 68mm (Chaparral, Garlic Bright, and Bulvana Odorless Garlic).
Also, our logo is only prominent on the EDTA label, but that product is our #1 seller and most recognizable, it is at the artist's discretion what to do with our logo. (attached, if needed).
Please show me only the label designs for "EDTA".
Target Market(s)
-Health-conscious adults over 40 in North America who buy herbal and/or dietary supplements.
-->Cardiovascular health-conscious adults (a.k.a., "heart healthy" adults)
-->Adults with poor cardiovascular health seeking naturopathic/alternative options.
Industry/Entity Type
Health And Wellness
Logo Text
Velmora Botanic
Colors
Designer to choose colors to be used in the design.

```html
<!DOCTYPE html>
<html lang="en">
<head>
<meta charset="utf-8">
<title>Velmora Botanic – EDTA Label</title>
<link rel="stylesheet" href="https://fonts.googleapis.com/css2?family=Montserrat:wght@300;400;500;600;700&display=swap">
<style>
  :root {
    --backdrop: #a3a3a3;
    --teal: #0e7a7e;
    --teal-deep: #0a5d61;
    --leaf-light: #3aa3a3;
    --leaf-dark: #11666a;
    --gold: #d9b866;
    --gold-pale: #f2e2b0;
    --ink-light: #eaf6f5;
  }
  * { margin: 0; padding: 0; box-sizing: border-box; }
  html, body {
    width: 1200px; height: 825px; overflow: hidden;
    background: var(--backdrop);
    font-family: "Montserrat", sans-serif;
  }
  .canvas {
    position: relative; width: 1200px; height: 825px;
    display: flex; align-items: center; justify-content: center;
  }
  .label {
    position: relative; width: 1100px; height: 400px;
    background: var(--teal);
    overflow: hidden;
  }
  .label-decor { position: absolute; inset: 0; }
  .label-copy {
    position: absolute; left: 300px; top: 44px; width: 340px;
    color: var(--ink-light);
  }
  .brand-line {
    font-size: 11px; font-weight: 600; letter-spacing: 0.55em;
    line-height: 1.7; text-transform: uppercase; color: var(--ink-light);
  }
  .brand-name {
    margin: 22px 0 0 0; text-align: center;
    display: flex; align-items: center; justify-content: center; gap: 10px;
    font-size: 20px; font-weight: 600; color: var(--gold);
  }
  .brand-dot {
    width: 14px; height: 14px; border-radius: 50%; background: var(--gold);
  }
  .product-name {
    margin-top: 30px; text-align: center;
    font-size: 52px; font-weight: 300; line-height: 1.1;
    letter-spacing: 0.04em; text-transform: uppercase; color: var(--ink-light);
  }
  .product-rule {
    width: 160px; height: 1px; background: var(--ink-light);
    margin: 22px auto 14px;
  }
  .product-claims {
    text-align: center; font-size: 9.5px; font-weight: 400;
    letter-spacing: 0.08em; line-height: 1.55; text-transform: uppercase;
  }
  .product-count {
    margin-top: 12px; text-align: center;
    font-size: 20px; font-weight: 700; line-height: 1;
  }
  .product-unit {
    text-align: center; font-size: 9.5px; font-weight: 500;
    letter-spacing: 0.08em; text-transform: uppercase; margin-top: 3px;
  }
</style>
</head>
<body>
<main class="canvas">
  <section class="label">
    <svg class="label-decor" width="1100" height="400" viewBox="0 0 1100 400">
      <defs>
        <linearGradient id="leafTone" x1="0" y1="0" x2="1" y2="1">
          <stop offset="0" stop-color="#3aa3a3"/>
          <stop offset="1" stop-color="#11666a"/>
        </linearGradient>
      </defs>
      <polygon class="botanical-band" role="img" aria-label="Botanical leaf illustration of herbal foliage"
        points="650,0 1100,0 1100,400 980,400 830,150 700,0" fill="url(#leafTone)"/>
      <polygon class="band-shade" points="700,0 830,150 980,400 940,400 810,170 680,0" fill="#0a5d61" opacity="0.6"/>
      <polyline class="gold-frame" points="640,0 810,290 1040,0" fill="none" stroke="#d9b866" stroke-width="3"/>
      <polyline class="gold-frame-thin" points="660,0 815,262 1020,0" fill="none" stroke="#f2e2b0" stroke-width="1"/>
      <line class="gold-frame-thin" x1="620" y1="0" x2="760" y2="400" stroke="#f2e2b0" stroke-width="1"/>
      <polygon class="botanical-corner" role="img" aria-label="Botanical leaf illustration in the lower corner"
        points="0,250 150,400 0,400" fill="url(#leafTone)"/>
      <polyline class="gold-frame" points="0,215 180,400" fill="none" stroke="#d9b866" stroke-width="3"/>
      <polyline class="gold-frame-thin" points="0,190 130,320 280,200" fill="none" stroke="#f2e2b0" stroke-width="1"/>
      <line class="gold-frame-thin" x1="255" y1="400" x2="290" y2="200" stroke="#f2e2b0" stroke-width="1"/>
    </svg>

    <div class="label-copy">
      <p class="brand-line">Velmora<br>Botanic</p>
      <p class="brand-name"><span class="brand-dot"></span>Velmora Botanic</p>
      <h1 class="product-name">EDTA</h1>
      <div class="product-rule"></div>
      <p class="product-claims">Heart Healthy<br>Cardio Support</p>
      <p class="product-count">90</p>
      <p class="product-unit">Capsules</p>
    </div>
  </section>
</main>
</body>
</html>
```